Kestrel Facilities Business Card Design

We would now like to design business cards with the new Kestrel Facilities logo

Target Market(s)

Professional

Industry/Entity Type

Professional services

Contact Information for Business Card

Employee name, title, phone number, email address, corporate office address and logo.

Font styles to use
Sans Serif

Colors
0054AA
0677BA
7BADD7
CADEEF
E8F1F8

Requirements
Must have
• My logo
Should not have
• any other pictures or images besides my logo

```html
<!DOCTYPE html>
<html lang="en">
<head>
<meta charset="utf-8">
<title>Kestrel Facilities – Business Card</title>
<link rel="stylesheet" href="https://fonts.googleapis.com/css2?family=Arimo:wght@400;700&family=Roboto+Condensed:wght@700&display=swap">
<style>
  :root {
    --backdrop: #d4d4d4;
    --card-white: #ffffff;
    --brand-blue: #0680e8;
    --brand-deep: #0054aa;
    --brand-mid: #0677ba;
    --ink: #1a1a1a;
  }
  * { margin: 0; padding: 0; box-sizing: border-box; }
  html, body { width: 1200px; height: 800px; overflow: hidden; }
  body {
    background: var(--backdrop);
    font-family: "Arimo", Arial, sans-serif;
    display: flex;
    align-items: center;
    justify-content: center;
    gap: 48px;
  }
  .card {
    position: relative;
    width: 525px;
    height: 300px;
    box-shadow: 0 6px 18px rgba(0,0,0,.18);
  }

  /* Front */
  .card--front { background: var(--card-white); color: var(--ink); }
  .brand {
    position: absolute;
    top: 38px;
    right: 36px;
    display: flex;
    align-items: center;
    gap: 12px;
    font-family: "Arimo", Arial, sans-serif;
    font-weight: 700;
    font-size: 26px;
    color: var(--brand-blue);
    letter-spacing: .5px;
  }
  .brand__square {
    width: 34px;
    height: 34px;
    border: 5px solid var(--brand-blue);
  }
  .holder {
    position: absolute;
    left: 36px;
    top: 130px;
  }
  .holder__name {
    font-family: "Roboto Condensed", "Arial Narrow", sans-serif;
    font-weight: 700;
    font-size: 25px;
    color: var(--brand-blue);
    text-transform: uppercase;
    line-height: 1;
  }
  .holder__title { font-size: 15px; margin-top: 3px; }
  .divider {
    position: absolute;
    left: 36px;
    right: 36px;
    top: 184px;
    height: 1px;
    background: var(--brand-blue);
  }
  .contact {
    position: absolute;
    left: 36px;
    top: 200px;
    list-style: none;
    font-size: 15px;
    line-height: 22px;
  }
  .contact li { display: flex; align-items: center; gap: 8px; }
  .contact svg { width: 14px; height: 14px; fill: var(--brand-blue); flex: none; }
  .contact .accent { color: var(--brand-blue); }
  .address {
    position: absolute;
    right: 36px;
    top: 200px;
    font-size: 15px;
    line-height: 20px;
    text-align: right;
    font-style: normal;
  }

  /* Back */
  .card--back {
    background: var(--brand-blue);
    display: flex;
    align-items: center;
    justify-content: center;
  }
  .brand--back {
    position: static;
    font-size: 34px;
    color: var(--brand-deep);
    gap: 14px;
  }
  .brand--back .brand__square { border-color: var(--brand-deep); width: 42px; height: 42px; border-width: 6px; }
</style>
</head>
<body>
  <section class="card card--front">
    <div class="brand"><span class="brand__square"></span><span>Kestrel Facilities</span></div>

    <div class="holder">
      <p class="holder__name">Daniel Reyes</p>
      <p class="holder__title">Managing Director</p>
    </div>

    <div class="divider"></div>

    <ul class="contact">
      <li>
        <svg viewBox="0 0 24 24" aria-hidden="true"><path d="M6.6 10.8a15.1 15.1 0 0 0 6.6 6.6l2.2-2.2a1 1 0 0 1 1-.25 11.4 11.4 0 0 0 3.6.57 1 1 0 0 1 1 1V20a1 1 0 0 1-1 1A17 17 0 0 1 3 4a1 1 0 0 1 1-1h3.5a1 1 0 0 1 1 1c0 1.25.2 2.45.57 3.6a1 1 0 0 1-.25 1z"/></svg>
        <span>055-210 384 617</span>
      </li>
      <li>
        <svg viewBox="0 0 24 24" aria-hidden="true"><path d="M2 5h20v14H2z M4 7v.5l8 5.5 8-5.5V7l-8 5.5z" fill-rule="evenodd"/></svg>
        <span>hello@kestrelfm.com</span>
      </li>
      <li>
        <svg viewBox="0 0 24 24" aria-hidden="true"><path d="M12 2a10 10 0 1 0 0 20 10 10 0 0 0 0-20zm-1 2.1V8H7.3A8 8 0 0 1 11 4.1zm2 0A8 8 0 0 1 16.7 8H13zM5.5 10H11v4H5.5a8 8 0 0 1 0-4zm7.5 0h5.5a8 8 0 0 1 0 4H13zm-5.7 6H11v3.9A8 8 0 0 1 7.3 16zm5.7 0h3.7a8 8 0 0 1-3.7 3.9z"/></svg>
        <span>www.<span class="accent">kestrelfm</span>.com</span>
      </li>
    </ul>

    <address class="address">
      88, Harbour Row, Suite 4<br>
      30917, Northfield
    </address>
  </section>

  <section class="card card--back">
    <div class="brand brand--back"><span class="brand__square"></span><span>Kestrel Facilities</span></div>
  </section>
</body>
</html>
```